full stationary design for a modern sleek design company

we are a design company that does modern minimalistic interior design works as well as other design services for high end clients.
we need a full stationary design including and not limited to (double sided business card, letter head, envelopes, documents folder...etc) that reflects the modern style design we do.
sleek modern and minimalistic is the requirements.
Updates

please use the latest attached files as there was a slight modification on the logo Added Wednesday, March 1, 2017

minor update on the logo files in JPG and PSD has been updated kindly follow the new attachments. Added Thursday, March 2, 2017

Target Market(s)

modern minimalist clients

Industry/Entity Type

Design Agency

Requirements
Must have
• the logo
Nice to have
• i like the colors in the colored 3D logo attached
Should not have
• too many colors

```html
<!DOCTYPE html>
<html lang="en">
<head>
<meta charset="utf-8">
<title>Linea Atelier – Business Card</title>
<link rel="stylesheet" href="https://fonts.googleapis.com/css2?family=Open+Sans:wght@400;600&display=swap">
<style>
  :root {
    --backdrop: #e7e5e2;
    --card-front: #ffffff;
    --card-back: #343535;
    --ink: #3a3a3a;
    --accent: #f28c1e;
    --faint: #f1f1f1;
    --white: #ffffff;
  }
  * { margin: 0; padding: 0; box-sizing: border-box; }
  html, body {
    width: 1200px; height: 987px; overflow: hidden;
    background: var(--backdrop);
    font-family: "Open Sans", Arial, sans-serif;
    color: var(--ink);
  }
  .stage { position: relative; width: 1200px; height: 987px; }

  .card {
    position: absolute; left: 293px; width: 615px; height: 350px;
    box-shadow: 0 3px 10px rgba(0,0,0,0.18);
  }
  .card--front { top: 130px; background: var(--card-front); }
  .card--back { top: 506px; background: var(--card-back); }

  .brand {
    position: absolute; display: flex; align-items: center; gap: 10px;
  }
  .brand__square { width: 22px; height: 22px; background: var(--accent); }
  .brand__name { font-weight: 600; letter-spacing: 2px; text-transform: uppercase; }

  .card--front .brand { left: 41px; top: 52px; }
  .card--front .brand__name { font-size: 24px; color: var(--ink); }

  .address { position: absolute; left: 41px; top: 165px; font-size: 15px; line-height: 23px; }

  .contacts { position: absolute; left: 41px; top: 216px; list-style: none; font-size: 15px; }
  .contacts li { display: flex; align-items: center; gap: 9px; height: 23.5px; }
  .contacts svg { width: 15px; height: 15px; fill: var(--accent); flex: none; }

  .decor-block {
    position: absolute; left: 305px; top: 171px; width: 135px; height: 135px;
    background: var(--faint);
  }

  .holder { position: absolute; right: 41px; top: 213px; text-align: right; }
  .holder__name { font-size: 20px; font-weight: 600; color: var(--accent); line-height: 26px; text-transform: uppercase; }
  .holder__role { font-size: 15px; line-height: 22px; color: var(--ink); }

  .card--back .brand { left: 0; right: 0; top: 148px; justify-content: center; gap: 14px; }
  .card--back .brand__square { width: 34px; height: 34px; }
  .card--back .brand__name { font-size: 40px; color: var(--white); letter-spacing: 4px; }

  .back-url {
    position: absolute; left: 0; right: 0; top: 285px; text-align: center;
    color: var(--white); font-size: 15px; letter-spacing: 4.5px;
  }
</style>
</head>
<body>
<main class="stage">

  <section class="card card--front" aria-label="Business card front">
    <div class="brand">
      <span class="brand__square"></span>
      <span class="brand__name">Linea Atelier</span>
    </div>

    <p class="address">214 Cedar Row<br>Portland, Oregon 97201</p>

    <ul class="contacts">
      <li>
        <svg viewBox="0 0 16 16" aria-hidden="true"><path d="M3.6 1.2l2.3 2.6-1.3 1.8c.9 2 2.6 3.7 4.6 4.6l1.8-1.3 2.6 2.3-1.2 2.2C7.5 15.1.9 8.5 1.4 2.4z"/></svg>
        <span>(555) 201 4482</span>
      </li>
      <li>
        <svg viewBox="0 0 16 16" aria-hidden="true"><path d="M4.5 0h7a1 1 0 0 1 1 1v14a1 1 0 0 1-1 1h-7a1 1 0 0 1-1-1V1a1 1 0 0 1 1-1zm.5 2v10h6V2zm3 11a1 1 0 1 0 0 2 1 1 0 0 0 0-2z"/></svg>
        <span>(555) 310 7756</span>
      </li>
      <li>
        <svg viewBox="0 0 16 16" aria-hidden="true"><path d="M1 3h14v10H1zm1.5 1.3v.4L8 8.6l5.5-3.9v-.4z"/></svg>
        <span>adam@lineaatelier.com</span>
      </li>
      <li>
        <svg viewBox="0 0 16 16" aria-hidden="true"><circle cx="8" cy="8" r="7"/><path d="M1 8h14M8 1c2.5 2.5 2.5 11.5 0 14M8 1c-2.5 2.5-2.5 11.5 0 14" stroke="#fff" stroke-width="1.1" fill="none"/></svg>
        <span>www.lineaatelier.com</span>
      </li>
    </ul>

    <div class="decor-block" aria-hidden="true"></div>

    <div class="holder">
      <p class="holder__name">Adam Reyes</p>
      <p class="holder__role">CEO&amp;Founder</p>
    </div>
  </section>

  <section class="card card--back" aria-label="Business card back">
    <div class="brand">
      <span class="brand__square"></span>
      <span class="brand__name">Linea Atelier</span>
    </div>
    <p class="back-url">www.lineaatelier.com</p>
  </section>

</main>
</body>
</html>
```